Systems and Technology Consultants - Website

Design & Build a website for a new company which operates in the Systems and Technology space for Transportation, Government and Commercial sectors.

Overall design should be minimalist in nature.
Should also have a feed that provides news and event updates on the main page.
Logo has already been awarded and should be incorporated into the site.

We like the overall layout, functionality and simplicity of the below sites. Submitted designs could be similar to or a combination of the aspects on these sites, or perhaps a whole different concept - we are open to new ideas.
Norvique.com
Teblo.it

Update 1 Dated 27 May 2014

All I am moving away from the Teblo.it website and would like it to be more aligned with Norvique.com not only in layout but in functionality. I will be extending the deadline of this design brief for two weeks to incorporate additional requirements and will add addtional funding to the project.

Apologies for not having more information available to provide but with so many submissions its getting confusing.

Thanks Derek

Please note that the brief has been updated and the deadline has been extended.

Important: We will need two language versions of the website, English and Arabic; the website is hosted on HostPelican

Hello All, Thank you for your submissions. We have narrowed it down to the final 6 designers and I just wanted to take a moment and provide a bit of feedback regarding the concepts that we like and the modifications we are looking for. First, let me mention some of the design functions we like. - At the top of the homepage we really like the "region" or "language" tab so that the website can be viewed in both English and Arabic. - We like the homepage to have clear color variation so that the different sections of the homepage are distinct. Additionally, we like the bottom portion of the homepage to be in red. We feel that draws attention to our contact information. Again, we would like the colors to integrate black, gray-scale, red, etc. - Having a search tab at the top of the home page, or integrated into the main image, so that the site is easy to navigate. - We especially like the main image to have the scrolling tabs at the bottom so it is easy to browse the services offered (Consultancy, Solutions Architecture, Masters Systems Integration, Independent Design Review). - In regards to the services offered tab we really like the idea that a few people presented that have the outside of our logo with an icon in the middle of consultancy, solutions, etc., etc. Secondly, as mentioned in our brief we really enjoy the design of norvique site. Specially, we enjoy the strong iconic images they use, the way the tabs at the top scroll easily, and contact us page that generates an email. Lastly, I've included some photos of the concept we have been working on. What we are trying to demonstrate is how our company offers a range of services that are essentially linked together. We provide individual services that when combined present the full service package. We would like this concept to be integrated into the over concept of our website. Please feel free to ask for clarification of any of the above points or contact us if you have any additional questions. We appreciate all of your hard work and are very excited to see the updated designs. Best, Marta Vennick Quelbrant Senior Program Manager marta.vennick@quelbrant-example.com

Industry/Entity Type

Government

Font styles to use
Serif
Sans Serif

Requirements
Must have
• Must work on/adapt to various/mobile devices (responsive)
Must be simple and straightforward
Colors should be in line/matching with logo
2 language versions: English and Arabic (no Thai)
Services should be the first group/row of items after/below the main image
Note: the website will be hosted by hostpelican
Nice to have
• Submit feedback form
What's New section
The banner at the bottom of the site should not be too large; we would like a narrow one more
It would be nice if the header/top banner (with Home, About, etc. tabs) could stay in place as you scroll down (like Norvique and Chatterloop)
We will likely only use one image with a Company slogan on the Home page rather than a carousel of images to rotate through
Should not have
• This is the existing website: http://www.quelbrant-example.org
We do not like the animation, the way the banner icons/titles bounce
Not simple enough, we don't like the functionality or how pages load so slowly
We do not like the logo centered - it should be at the left
The banner and its tabs should not be towards the right, we would like them to be centered, to go all the way across and to be below the logo

```html
<!DOCTYPE html>
<html lang="en">
<head>
<meta charset="utf-8">
<title>Quelbrant – Systems Professionals</title>
<link href="https://fonts.googleapis.com/css2?family=Open+Sans:wght@400;600;700&display=swap" rel="stylesheet">
<style>
:root{
  --red:#e8343f;
  --ink:#1f1f1f;
  --text:#3a3a3a;
  --line:#dcdcdc;
  --footer:#3b3b3d;
  --footer-deep:#2e2e30;
  --panel:#535356;
  --white:#ffffff;
}
*{margin:0;padding:0;box-sizing:border-box}
html,body{width:726px;height:1200px;overflow:hidden;background:var(--white)}
body{font-family:"Open Sans",Arial,sans-serif;color:var(--text);position:relative}
.abs{position:absolute}

/* header */
.brand{left:104px;top:30px;width:90px;height:20px;display:flex;align-items:center;gap:6px}
.brand-dot{width:8px;height:8px;border-radius:50%;background:var(--red)}
.brand-name{font-size:11px;font-weight:700;color:var(--red);letter-spacing:1px}
.search-label{left:410px;top:34px;font-size:7.5px;font-weight:600;color:var(--ink)}
.search-field{left:443px;top:30px;width:151px;height:17px;background:#efefef;font-size:6px;color:#666;padding:5px 9px}
.search-field::after{content:"";position:absolute;right:9px;top:7px;border:2.5px solid transparent;border-top:3px solid #333}
.search-btn{left:600px;top:30px;width:19px;height:19px;background:#2b2b2b}

/* navigation */
.main-nav{left:0;top:78px;width:726px;height:33px;background:linear-gradient(#f05a62,var(--red))}
.main-nav a{position:absolute;top:12px;font-size:7.4px;font-weight:600;color:var(--white);text-decoration:none}

/* hero */
.hero{left:0;top:111px;width:726px;height:295px;background:linear-gradient(110deg,#c9d9e8 0%,#eef3f8 35%,#aec4d9 65%,#7f9cb9 100%)}
.hero-arrow{top:121px;width:19px;height:21px;background:#1e1e1e}
.hero-caption{left:41px;top:184px;width:259px;height:42px;background:rgba(45,45,50,.82);color:var(--white);font-size:16px;font-weight:600;padding:10px 0 0 33px;letter-spacing:.4px}

/* services */
.service{top:434px;width:101px;height:100px;border:1px solid var(--line);text-align:center}
.service svg{margin-top:13px}
.service h3{font-size:8.6px;font-weight:600;color:var(--ink);margin-top:6px}
.service p{font-size:6.3px;line-height:11px;margin-top:6px}

/* section headings */
.section-title{font-size:10.5px;font-weight:600;color:var(--ink)}
.stripe{height:7px;background:repeating-linear-gradient(135deg,#e4e4e4 0 1px,transparent 1px 3px)}
.body-text{font-size:6.2px;line-height:11.7px;color:var(--text);letter-spacing:-0.15px}
.photo{background:linear-gradient(135deg,#9fb3c7,#e9eef3 55%,#b8a48c)}

/* news */
.cal{left:96px;width:37px;height:36px;background:#f4f4f4;box-shadow:0 1px 2px rgba(0,0,0,.25);text-align:center}
.cal::before{content:"";display:block;height:6px;background:var(--red)}
.cal span{display:block;font-size:7.4px;font-weight:700;color:#555;line-height:10px;margin-top:4px}
.news-text{left:144px;width:152px;font-size:6.3px;line-height:11px;text-align:justify;letter-spacing:-0.1px}
.news-rule{left:96px;width:200px;height:1px;background:#ececec}

/* footer */
.site-footer{left:0;top:978px;width:726px;height:172px;background:var(--footer)}
.footer-bar{left:0;top:1150px;width:726px;height:50px;background:var(--footer-deep)}
.footer-title{font-size:10.5px;font-weight:600;color:var(--white)}
.quote{left:95px;top:1034px;width:167px;height:70px;background:var(--panel);color:var(--white);font-size:6.3px;line-height:11.7px;padding:8px 12px;text-align:justify}
.quote::after{content:"";position:absolute;right:16px;bottom:-14px;border-left:16px solid transparent;border-top:14px solid var(--panel)}
.links a{display:block;font-size:6.3px;color:var(--white);text-decoration:none;line-height:13.5px}
.contact-row{left:464px;width:200px;height:16px;color:var(--white);font-size:6.3px}
.contact-row span{position:absolute;left:29px;top:4px}
.copyright{left:94px;top:1171px;font-size:6.5px;color:var(--white)}
.social{top:1169px;width:14px;height:14px;border-radius:50%;background:var(--white)}
</style>
</head>
<body>

<header>
  <div class="abs brand"><div class="brand-dot"></div><div class="brand-name">QUELBRANT</div></div>
  <div class="abs search-label">SEARCH</div>
  <div class="abs search-field">Articles</div>
  <div class="abs search-btn">
    <svg width="19" height="19" viewBox="0 0 19 19"><circle cx="8.5" cy="8.5" r="3.6" fill="none" stroke="#fff" stroke-width="1.4"/><line x1="11" y1="11" x2="14" y2="14" stroke="#fff" stroke-width="1.6"/></svg>
  </div>
</header>

<nav class="abs main-nav">
  <a href="#" style="left:103px">HOME</a>
  <a href="#" style="left:157px">BUSINESS UNITS</a>
  <a href="#" style="left:246px">ABOUT US</a>
  <a href="#" style="left:315px">SERVICES</a>
  <a href="#" style="left:383px">LOCATIONS</a>
  <a href="#" style="left:457px">NEWS &amp; EVENTS</a>
  <a href="#" style="left:545px">CONTACT US</a>
</nav>

<section class="abs hero" role="img" aria-label="Photo of two engineers reviewing work on a laptop in a bright glass office">
  <div class="abs hero-arrow" style="left:0"><svg width="19" height="21"><polyline points="12,5 7,10.5 12,16" fill="none" stroke="#fff" stroke-width="2.2"/></svg></div>
  <div class="abs hero-arrow" style="left:707px"><svg width="19" height="21"><polyline points="7,5 12,10.5 7,16" fill="none" stroke="#fff" stroke-width="2.2"/></svg></div>
  <div class="abs hero-caption">SYSTEMS PROFESSIONALS</div>
</section>

<section class="services">
  <div class="abs service" style="left:95px">
    <svg width="22" height="22" viewBox="0 0 22 22"><circle cx="11" cy="8" r="5" fill="#e8343f"/><path d="M3 21c0-5 4-7 8-7s8 2 8 7z" fill="#e8343f"/></svg>
    <h3>CONSULTING</h3><p>Morbi interdum mollis sapien.<br>Sed ac risus. Phasellus</p></div>
  <div class="abs service" style="left:203px">
    <svg width="28" height="22" viewBox="0 0 28 22"><circle cx="8" cy="7" r="4.5" fill="none" stroke="#e8343f" stroke-width="2"/><rect x="11" y="9" width="14" height="9" fill="none" stroke="#e8343f" stroke-width="1.6"/><line x1="9" y1="20" x2="27" y2="20" stroke="#e8343f" stroke-width="1.6"/></svg>
    <h3>ENGINEERING</h3><p>Morbi interdum mollis sapien.<br>Sed ac risus. Phasellus</p></div>
  <div class="abs service" style="left:310px">
    <svg width="22" height="22" viewBox="0 0 22 22"><path d="M5 8a6 6 0 0 1 12 0z" fill="#e8343f"/><circle cx="11" cy="11" r="3.5" fill="#e8343f"/><path d="M4 22c0-5 3-7 7-7s7 2 7 7z" fill="#e8343f"/></svg>
    <h3>CONSTRUCTION</h3><p>Morbi interdum mollis sapien.<br>Sed ac risus. Phasellus</p></div>
  <div class="abs service" style="left:418px">
    <svg width="26" height="22" viewBox="0 0 26 22"><circle cx="9" cy="12" r="6.5" fill="none" stroke="#e8343f" stroke-width="3.4" stroke-dasharray="3 2"/><circle cx="19" cy="7" r="4" fill="none" stroke="#e8343f" stroke-width="2.6" stroke-dasharray="2 1.6"/></svg>
    <h3>OPERATIONS</h3><p>Morbi interdum mollis sapien.<br>Sed ac risus. Phasellus</p></div>
  <div class="abs service" style="left:527px">
    <svg width="22" height="22" viewBox="0 0 22 22"><line x1="3" y1="19" x2="17" y2="5" stroke="#e8343f" stroke-width="3"/><line x1="4" y1="3" x2="19" y2="19" stroke="#e8343f" stroke-width="3"/><circle cx="17" cy="5" r="3.5" fill="#e8343f"/></svg>
    <h3>MAINTENANCE</h3><p>Morbi interdum mollis sapien.<br>Sed ac risus. Phasellus</p></div>
</section>

<section class="vision">
  <h2 class="abs section-title" style="left:97px;top:560px">QUELBRANT OUR VISION</h2>
  <div class="abs stripe" style="left:235px;top:564px;width:395px"></div>
  <div class="abs photo" style="left:95px;top:596px;width:92px;height:66px" role="img" aria-label="Photo of a smiling team member with colleagues"></div>
  <p class="abs body-text" style="left:209px;top:595px;width:422px;text-align:justify">quelbrant specializes in delivering quality professional services and technical projects that support larger business goals. systems are tools that support a greater business function and need. We Understand that Most Technical Projects are conceptualized to support A larger Vision with Actual business goals in Mind and ensure that all of our Professional and Certified Expertise is Included in our Professional Services to meet those goals. Quelbrant recognizes The MIDDLE East and Greater Asia regions are. economic growth markets with developing infrastructure projects requiring specialist systems and technical expertise. accordingly, its Presence in Quelbrant has Evolved The regions to meet Client demands and expectations.</p>
  <p class="abs body-text" style="left:95px;top:677px;width:540px">our Ultimate Goal is to provide Quality, Technical and Professional Services on Projects of any scale and / or complexity, from Conception through to completion. our philosophy is simple; stick to what you are good at and be the best at it.</p>
</section>

<section class="news">
  <h2 class="abs section-title" style="left:97px;top:733px">NEWS &amp; EVENTS</h2>
  <div class="abs stripe" style="left:182px;top:737px;width:125px"></div>
  <div class="abs cal" style="top:770px"><span>July 14<br>2014</span></div>
  <p class="abs news-text" style="top:770px">In ultricies pellentesque massa a porta. Aliquam ipsum enim, hendrerit ut porta nec. ullamcorper et nulla. In eget mi dui, sit amet.</p>
  <div class="abs news-rule" style="top:815px"></div>
  <div class="abs cal" style="top:828px"><span>Aug 4<br>2014</span></div>
  <p class="abs news-text" style="top:828px">In ultricies pellentesque massa a porta. Aliquam ipsum enim, hendrerit ut porta nec. ullamcorper et nulla. In eget mi dui, sit amet.</p>
  <div class="abs news-rule" style="top:874px"></div>
  <div class="abs cal" style="top:886px"><span>Nov 22<br>2014</span></div>
  <p class="abs news-text" style="top:888px">In ultricies pellentesque massa a porta. Aliquam ipsum enim, hendrerit ut porta nec. ullamcorper et nulla. In eget mi dui, sit amet.</p>
</section>

<section class="goals">
  <h2 class="abs section-title" style="left:334px;top:733px">OUR GOALS</h2>
  <div class="abs stripe" style="left:401px;top:737px;width:229px"></div>
  <div class="abs photo" style="left:334px;top:764px;width:72px;height:60px" role="img" aria-label="Photo of a business team standing together"></div>
  <p class="abs body-text" style="left:416px;top:760px;width:218px;text-align:justify">we have the expertise to deliver the exclusive system. And technical quality. To support and accommodate larger business goals. Our management system is a tool that supports the model and business needs. We understand that the most technical concepts that support the vision of a true business goals. We will take steps to ensure that the knowledge and expertise of our. Be in the professional services we deliver to our customers</p>
  <p class="abs body-text" style="left:333px;top:843px;width:301px;text-align:justify">we believe that the Zone East and Asia. A market that is growing the economy and Programmes. Developed infrastructure Which requires management systems and specialized. Therefore, we begin the process of expanding into the Middle East and Asia. To meet needs And expectations of our customers is our ultimate goal is to provide quality service. And also to a specific system, we have the expertise, particularly relentless. Whether the project is small or large. And a more complex one at that. From the start until the project is complete. Our philosophy is based on the principles. Commitment to something as well. And development to move towards excellence.</p>
</section>

<footer>
  <div class="abs site-footer"></div>
  <h2 class="abs footer-title" style="left:95px;top:1002px">Testimonials</h2>
  <div class="abs quote">we believe that the Zone East and Asia. A market that is growing the economy and Programmes. Developed infrastructure Which requires management systems and specialized. Therefore</div>
  <p class="abs" style="left:94px;top:1116px;font-size:7px;color:#fff">-Evan Mercer</p>

  <h2 class="abs footer-title" style="left:324px;top:1002px">Useful Links</h2>
  <div class="abs links" style="left:325px;top:1027px">
    <a href="#">HOME</a><a href="#">BUSINESS UNITS</a><a href="#">ABOUT US</a><a href="#">SERVICES</a><a href="#">LOCATIONS</a><a href="#">&nbsp;NEWS &amp; EVENTS</a><a href="#">CONTACT US</a>
  </div>

  <h2 class="abs footer-title" style="left:464px;top:1002px">Contact Us</h2>
  <div class="abs contact-row" style="top:1040px">
    <svg width="22" height="14" viewBox="0 0 22 14"><path d="M1 5c3-5 17-5 20 0l-4 2-1-2c-3-1-7-1-10 0l-1 2z" fill="#fff"/><rect x="5" y="7" width="12" height="7" rx="1.5" fill="#fff"/></svg>
    <span>(555)-014-2276</span></div>
  <div class="abs contact-row" style="top:1068px">
    <svg width="16" height="16" viewBox="0 0 16 16"><path d="M2 14l1-4 9-9 3 3-9 9z" fill="#fff"/></svg>
    <span>hello@quelbrant-example.com</span></div>
  <div class="abs contact-row" style="top:1096px">
    <svg width="16" height="16" viewBox="0 0 16 16"><circle cx="6" cy="5" r="3.5" fill="#fff"/><path d="M1 16c0-5 2-7 5-7s5 2 5 7z" fill="#fff"/></svg>
    <span>18 Harlow Bend, Ashcombe, SC 20410</span></div>

  <div class="abs footer-bar"></div>
  <p class="abs copyright">© Copyright 2014 <b>QUELBRANT</b>. All rights reserved.</p>
  <div class="abs social" style="left:529px" aria-label="Social profile"></div>
  <div class="abs social" style="left:556px" aria-label="Social profile"></div>
  <div class="abs social" style="left:585px" aria-label="Social profile"></div>
</footer>

</body>
</html>
```